Garlic Farm for Farm Sales/Restaurant sales

Need a professional, but appealing to agriculture world. We are selling 27 kinds of Organic Garlic from a farm in Simla,CO. I have uploaded logo and business information-we are going to need a template, because I will need to use it for four separate people.
-We are trying to appeal to Farm to table restaurants
-As well as growers/farmers

Target Market(s)

Agriculture Sales/Restaurants-Organic

Industry/Entity Type

Agriculture

Contact Information for Business Card

Want it to look more unique then your average kelto stock card- I want it to look amazing

Font styles to use
Sans Serif

Colors
0455a3
ec1f27
fbed22
ffffff

Requirements
Must have
• Just be creative
Nice to have
• Colorful
Should not have
• plain

```html
<!DOCTYPE html>
<html lang="en">
<head>
<meta charset="utf-8">
<title>Ridgeline Gourmet Garlic – Business Card</title>
<link rel="stylesheet" href="https://fonts.googleapis.com/css2?family=Open+Sans:ital,wght@0,400;0,600;0,700;1,600&display=swap">
<style>
  :root {
    --navy: #0c2d5e;
    --red: #c00a2a;
    --yellow: #f7c81e;
    --white: #ffffff;
    --grey-text: #555a60;
    --divider: #b9bcc0;
    --backdrop: #e9e7e4;
  }
  * { margin: 0; padding: 0; box-sizing: border-box; }
  html, body {
    width: 1200px; height: 987px; overflow: hidden;
    background: var(--backdrop);
    font-family: "Open Sans", Arial, sans-serif;
  }
  .card {
    position: absolute; left: 293px; width: 615px; height: 351px;
    box-shadow: 0 3px 10px rgba(0,0,0,.25);
    overflow: hidden;
  }
  .card--front { top: 130px; background: var(--white); }
  .card--back { top: 506px; background: var(--red); }

  /* front: brand */
  .brand {
    position: absolute; left: 0; right: 0; top: 28px;
    display: flex; flex-direction: column; align-items: center;
  }
  .brand__dot {
    width: 96px; height: 96px; border-radius: 50%;
    background: var(--red);
  }
  .brand__name {
    margin-top: 14px; font-weight: 700; font-size: 30px;
    color: var(--navy); letter-spacing: .5px; line-height: 1;
  }
  .brand__tagline {
    margin-top: 6px; font-weight: 700; font-size: 12px;
    color: var(--navy); letter-spacing: 3px; text-transform: uppercase;
  }

  /* front: contact row */
  .contact-row {
    position: absolute; top: 242px; left: 0; right: 0; height: 54px;
  }
  .person { position: absolute; left: 33px; top: 3px; }
  .person__name { font-weight: 700; font-size: 20px; color: var(--navy); line-height: 1.2; }
  .person__role { font-size: 15px; color: var(--red); line-height: 1.35; }
  .divider {
    position: absolute; top: 0; width: 1.5px; height: 52px; background: var(--divider);
  }
  .divider--one { left: 198px; }
  .divider--two { left: 380px; }
  .address {
    position: absolute; left: 198px; width: 182px; top: 6px;
    text-align: center; font-size: 15px; color: var(--grey-text); line-height: 1.5;
  }
  .reach { position: absolute; left: 411px; top: 6px; font-size: 15px; color: var(--grey-text); line-height: 1.5; }
  .reach__line { display: flex; align-items: center; gap: 8px; }
  .reach__line svg { width: 14px; height: 14px; fill: var(--navy); flex: none; }

  /* front: footer bands */
  .band { position: absolute; left: 0; right: 0; bottom: 0; height: 40px; }
  .band svg { display: block; }
  .web {
    position: absolute; right: 24px; bottom: 8px;
    font-style: italic; font-weight: 600; font-size: 16px;
    color: var(--white); letter-spacing: 2.5px;
  }

  /* back */
  .back-brand {
    position: absolute; left: 444px; top: 164px; width: 120px;
    display: flex; flex-direction: column; align-items: center;
  }
  .back-brand__dot {
    width: 104px; height: 104px; border-radius: 50%; background: var(--navy);
  }
  .back-brand__name {
    margin-top: 6px; font-weight: 700; font-size: 15px; color: var(--yellow); line-height: 1;
  }
  .social {
    position: absolute; left: 464px; top: 312px; display: flex; gap: 3px;
  }
  .social__dot {
    width: 18px; height: 18px; border-radius: 50%;
    border: 1.5px solid var(--yellow);
  }
</style>
</head>
<body>
  <section class="card card--front">
    <div class="brand">
      <div class="brand__dot"></div>
      <div class="brand__name">Ridgeline</div>
      <div class="brand__tagline">Gourmet Garlic</div>
    </div>

    <div class="contact-row">
      <div class="person">
        <div class="person__name">OWEN HARLOW</div>
        <div class="person__role">CEO/FOUNDER</div>
      </div>
      <span class="divider divider--one"></span>
      <div class="address">P.O. Box 12 Alder<br>CO&nbsp; 80000</div>
      <span class="divider divider--two"></span>
      <div class="reach">
        <div class="reach__line">
          <svg viewBox="0 0 24 24" aria-hidden="true"><path d="M6.6 10.8a15.1 15.1 0 0 0 6.6 6.6l2.2-2.2a1 1 0 0 1 1-.25 11.4 11.4 0 0 0 3.6.57 1 1 0 0 1 1 1V20a1 1 0 0 1-1 1A17 17 0 0 1 3 4a1 1 0 0 1 1-1h3.5a1 1 0 0 1 1 1c0 1.25.2 2.45.57 3.57a1 1 0 0 1-.25 1z"/></svg>
          555-014-2273
        </div>
        <div class="reach__line">
          <svg viewBox="0 0 24 24" aria-hidden="true"><path d="M2 5h20v14H2z M2 5l10 8 10-8" fill="var(--navy)"/><path d="M3 6l9 7 9-7" fill="none" stroke="#fff" stroke-width="1.8"/></svg>
          Dana@RLGarlic.com
        </div>
      </div>
    </div>

    <div class="band">
      <svg width="615" height="40" viewBox="0 0 615 40" aria-hidden="true">
        <polygon points="0,27 183,27 180,33 0,33" fill="var(--red)"/>
        <polygon points="186,27 355,27 352,33 183,33" fill="var(--yellow)"/>
        <polygon points="0,33 615,33 615,40 0,40" fill="var(--navy)"/>
        <polygon points="372,9 615,9 615,40 352,40" fill="var(--navy)"/>
      </svg>
      <div class="web">www.RLGarlic.com</div>
    </div>
  </section>

  <section class="card card--back">
    <div class="back-brand">
      <div class="back-brand__dot"></div>
      <div class="back-brand__name">Ridgeline</div>
    </div>
    <div class="social" aria-label="Social media links">
      <span class="social__dot"></span>
      <span class="social__dot"></span>
      <span class="social__dot"></span>
      <span class="social__dot"></span>
    </div>
  </section>
</body>
</html>
```